Cozy Cradle Loops Needs a Beautiful Website

I need a new website for this new E-commerce. I sell handmade baby crochets, e.g. booties, headbands, hats, etc. I need a feminine and soft design to make the moms-to-be say 'oohh ahh'. I'd like pink, blue and gray. I'd like an inviting homepage, and nice regular pages where people can see and order the products.

Industry/Entity Type

Baby

Requirements
Must have
• beautiful, soft, feminine design. Please use pictures of the colors I'd like: brown, yellow, pink and blue. Any combination, but definitely include brown.

```html
<!DOCTYPE html>
<html lang="en">
<head>
<meta charset="utf-8">
<title>Cozy Cradle Loops</title>
<link href="https://fonts.googleapis.com/css2?family=Quicksand:wght@400;500;600;700&family=Open+Sans:wght@400;600;700&display=swap" rel="stylesheet">
<style>
:root{
  --pink:#e8358a;
  --blue:#1bb5d9;
  --blue-dark:#12a0c3;
  --grey-text:#8a8a8a;
  --grey-dark:#555;
  --grey-line:#e4e4e4;
  --footer-bg:#f4f4f4;
  --white:#fff;
}
*{margin:0;padding:0;box-sizing:border-box}
html,body{width:759px;height:1200px;overflow:hidden;background:var(--white)}
body{position:relative;font-family:"Open Sans",sans-serif;color:var(--grey-dark)}
.abs{position:absolute}
.top-rule{left:0;top:4px;width:759px;border-top:1px dashed var(--pink)}
.util-links{right:75px;top:13px;font-size:8.5px;color:var(--grey-text)}
.util-links span{margin:0 3px}
.brand{left:76px;top:36px;display:flex;align-items:center;gap:8px;font-family:"Quicksand",sans-serif;font-weight:700;font-size:21px;color:var(--pink)}
.brand-dot{width:14px;height:14px;border-radius:50%;background:var(--blue)}
.search{left:296px;top:49px;width:240px;height:26px;border:1.5px solid #e2e2e2;border-radius:13px;font-size:8px;color:#9a9a9a;padding:7px 12px}
.search svg{position:absolute;right:8px;top:5px}
.cart-icon{left:614px;top:48px}
.cart-text{left:641px;top:51px;font-family:"Quicksand",sans-serif;font-size:10px;color:var(--grey-dark);line-height:12px}
.cart-text b{display:block;color:var(--pink);font-weight:500;font-size:12px}
.nav{left:75px;top:90px;width:609px;height:32px;background:linear-gradient(var(--blue),var(--blue-dark));display:flex}
.nav a{color:var(--white);text-decoration:none;font-family:"Quicksand",sans-serif;font-weight:600;font-size:11.5px;display:flex;align-items:center;justify-content:center;border-right:1px solid rgba(0,0,0,.1)}
.nav a:last-child{border-right:none}
.hero{left:75px;top:122px;width:609px;height:254px;border:3px solid #ececec;background:var(--white)}
.hero h1{position:absolute;left:44px;top:64px;font-family:"Quicksand",sans-serif;font-weight:500;font-size:24px;color:var(--pink);white-space:nowrap}
.hero h2{position:absolute;left:44px;top:96px;font-family:"Quicksand",sans-serif;font-weight:500;font-size:14px;color:var(--blue);white-space:nowrap}
.hero p{position:absolute;left:44px;top:120px;width:250px;font-size:7.5px;line-height:12.5px;color:var(--grey-text)}
.btn{background:var(--pink);color:var(--white);font-weight:700;font-size:7.5px;text-transform:uppercase;display:flex;align-items:center;justify-content:center;border-radius:2px}
.hero .btn{position:absolute;left:44px;top:149px;width:82px;height:24px;font-size:8px}
.hero-photo{position:absolute;left:314px;top:28px;width:250px;height:178px;background:linear-gradient(135deg,#7fd9ea,#3bbfd8)}
.dots-tab{left:346px;top:354px;width:66px;height:24px;background:#ececec;border-radius:14px 14px 0 0;display:flex;justify-content:center;align-items:center;gap:3px}
.dots-tab i{width:7px;height:7px;border-radius:50%;background:#a9a9a9}
.dots-tab i:first-child{background:var(--pink)}
.welcome{left:75px;top:405px;width:609px;text-align:center}
.welcome h3{font-family:"Quicksand",sans-serif;font-weight:500;font-size:19.5px;color:var(--grey-dark)}
.welcome p{margin-top:6px;font-size:7.6px;line-height:13px;color:var(--grey-text);padding:0 20px}
.divider{left:75px;top:507px;width:609px;border-top:1px solid var(--grey-line)}
.section-title{left:76px;top:534px;font-family:"Quicksand",sans-serif;font-weight:500;font-size:15px;color:var(--blue)}
.card{width:139px}
.card .photo{height:95px;border:1px solid #ddd}
.card .name{margin-top:5px;font-family:"Quicksand",sans-serif;font-weight:500;font-size:10.5px;color:var(--grey-dark)}
.card .desc{margin-top:3px;font-size:7px;line-height:12px;color:var(--grey-text)}
.card .btn{margin-top:5px;width:66px;height:18px;font-size:7px}
.footer{left:0;top:982px;width:759px;height:218px;background:var(--footer-bg);border-top:1px dashed #cfcfcf}
.fcol{top:1008px}
.fcol h4{font-family:"Quicksand",sans-serif;font-weight:500;font-size:15px;color:var(--grey-dark);margin-bottom:9px}
.fcol li{list-style:none;font-size:7.8px;line-height:16px;color:var(--grey-dark)}
.pay{left:518px;top:1119px;display:flex;gap:4px}
.pay span{width:23px;height:15px;border-radius:2px;border:1px solid #ccc}
.bottom-rule{left:0;top:1158px;width:759px;border-top:1px solid #e6e6e6}
.copyright{left:78px;top:1173px;font-size:7.8px;color:var(--grey-dark)}
.social{left:624px;top:1169px;display:flex;gap:6px}
.social span{width:14px;height:14px;border-radius:2px}
</style>
</head>
<body>
<div class="abs top-rule"></div>
<div class="abs util-links">View Cart<span>|</span>Register<span>|</span>Login<span>|</span>My Account</div>
<div class="abs brand"><span class="brand-dot"></span>Cozy Cradle Loops</div>
<div class="abs search">Type your word here
  <svg width="14" height="14" viewBox="0 0 14 14"><circle cx="6" cy="6" r="4.5" fill="none" stroke="#b5b5b5" stroke-width="1.5"/><line x1="9.3" y1="9.3" x2="13" y2="13" stroke="#b5b5b5" stroke-width="1.5"/></svg>
</div>
<svg class="abs cart-icon" width="21" height="26" viewBox="0 0 21 26"><path d="M6 9V6a4.5 4.5 0 0 1 9 0v3" fill="none" stroke="#c9c9c9" stroke-width="1.5"/><rect x="0" y="9" width="21" height="17" rx="1" fill="#d2d2d2"/></svg>
<div class="abs cart-text">My Cart<b>0 items</b></div>

<nav class="abs nav">
  <a style="width:65px">Home</a><a style="width:76px">About Us</a><a style="width:76px">Products</a><a style="width:71px">Specials</a><a style="width:83px">Order Now</a><a style="width:86px">Best Selling</a><a style="width:79px">Support</a><a style="width:73px">Contact</a>
</nav>

<section class="abs hero">
  <h1>We Sell Baby Crochets</h1>
  <h2>Morbi ullamcorper nonummy</h2>
  <p>Donec scelerisque leo ac risus Praesent sit amet est In dictum dolor eu dictum porttitor enim felis viverra mi eget luctus</p>
  <div class="btn">View Product</div>
  <div class="hero-photo" role="img" aria-label="Light blue crocheted baby crown"></div>
</section>
<div class="abs dots-tab"><i></i><i></i><i></i><i></i></div>

<section class="abs welcome">
  <h3>Welcome to Cozy Cradle Loops</h3>
  <p>Pellentesque faucibus Ut accumsan ultricies elit Maecenas at justo id velit placerat molestie Donec dictum lectus non odio Cras a ante vitae enim iaculis aliquam Mauris nunc quam venenatis nec euismod sit amet egestas placerat est Pellentesque habitant morbi tristique senectus et netus et malesuada fames ac turpis egestas Cras id elit Integer quis urna Ut ante enim dapibus malesuada fringilla eu condimentum quis tellus</p>
</section>
<div class="abs divider"></div>
<div class="abs section-title">Featured Products</div>

<div class="abs card" style="left:76px;top:564px"><div class="photo" role="img" aria-label="Black and white crocheted baby sneakers" style="background:linear-gradient(135deg,#4a4a4a,#8a8a8a)"></div><div class="name">Product Name</div><div class="desc">Donec dictum lectus non odio Cras ante vitae enim iaculis aliquam</div><div class="btn">Add to Cart</div></div>
<div class="abs card" style="left:228px;top:564px"><div class="photo" role="img" aria-label="Brown crocheted baby sneakers with pink star" style="background:linear-gradient(135deg,#8a7466,#5e4a3f)"></div><div class="name">Product Name</div><div class="desc">Donec dictum lectus non odio Cras ante vitae enim iaculis aliquam</div><div class="btn">Add to Cart</div></div>
<div class="abs card" style="left:378px;top:564px"><div class="photo" role="img" aria-label="Pink crocheted baby slippers with roses" style="background:linear-gradient(135deg,#ece6e2,#e3c3c9)"></div><div class="name">Product Name</div><div class="desc">Donec dictum lectus non odio Cras ante vitae enim iaculis aliquam</div><div class="btn">Add to Cart</div></div>
<div class="abs card" style="left:530px;top:564px"><div class="photo" role="img" aria-label="Navy crocheted baby high-top with red star" style="background:linear-gradient(135deg,#3a4aa0,#6a72a8)"></div><div class="name">Product Name</div><div class="desc">Donec dictum lectus non odio Cras ante vitae enim iaculis aliquam</div><div class="btn">Add to Cart</div></div>

<div class="abs card" style="left:76px;top:766px"><div class="photo" role="img" aria-label="Grey crocheted baby shoe with red flower" style="background:linear-gradient(135deg,#5d4a50,#8a8f96)"></div><div class="name">Product Name</div><div class="desc">Donec dictum lectus non odio Cras ante vitae enim iaculis aliquam</div><div class="btn">Add to Cart</div></div>
<div class="abs card" style="left:228px;top:766px"><div class="photo" role="img" aria-label="Denim blue crocheted baby sneakers" style="background:linear-gradient(135deg,#8e9096,#4a5b78)"></div><div class="name">Product Name</div><div class="desc">Donec dictum lectus non odio Cras ante vitae enim iaculis aliquam</div><div class="btn">Add to Cart</div></div>
<div class="abs card" style="left:378px;top:766px"><div class="photo" role="img" aria-label="Pink crocheted baby crown" style="background:linear-gradient(135deg,#f49ad4,#ec5fbd)"></div><div class="name">Product Name</div><div class="desc">Donec dictum lectus non odio Cras ante vitae enim iaculis aliquam</div><div class="btn">Add to Cart</div></div>
<div class="abs card" style="left:530px;top:766px"><div class="photo" role="img" aria-label="Cream crocheted baby shoes with roses" style="background:linear-gradient(135deg,#6b4a48,#d9d2bf)"></div><div class="name">Product Name</div><div class="desc">Donec dictum lectus non odio Cras ante vitae enim iaculis aliquam</div><div class="btn">Add to Cart</div></div>

<footer class="abs footer"></footer>
<div class="abs fcol" style="left:78px"><h4>Products</h4><ul><li>Name Labels</li><li>Clothing Labels</li><li>Shoe Labels</li><li>Stick On Clothing Labels</li><li>Backpacks</li></ul></div>
<div class="abs fcol" style="left:214px"><h4>Categories</h4><ul><li>Christmas</li><li>Halloween</li><li>Kids Bags</li><li>Stationery</li><li>Personalised Clothing</li></ul></div>
<div class="abs fcol" style="left:357px"><h4>Best Selling</h4><ul><li>Personalised Wooden Puzzles</li><li>Wooden Name Puzzle</li><li>Personalised Teddy Bear</li><li>Story Books</li><li>Backpacks</li></ul></div>
<div class="abs fcol" style="left:518px"><h4>Information</h4><ul><li>About Us</li><li>Order Now</li><li>Support</li><li>Shipping &amp; Return</li><li>Contact Us</li></ul></div>
<div class="abs pay"><span style="background:#c94a3a"></span><span style="background:#2d4f9e"></span><span style="background:#3a8fd0"></span><span style="background:#f1f1f1"></span></div>
<div class="abs bottom-rule"></div>
<div class="abs copyright">© 2014 Company Name&nbsp; All right reserved&nbsp; Term of Use</div>
<div class="abs social"><span style="background:#3b5a9a"></span><span style="background:#3fb0e3"></span><span style="background:#1c7eb6"></span></div>
</body>
</html>
```